Create the design of Sitelaunch (in photoshop or similar)

*edit* What we wanna see is a sketch of a first page, and then in the end 5 page designs, but the main page will be the big tasks other pages are just basically pop-ups or form. *edit*

We need a web design for our new startup Sitelaunch in turn will be providing web pages to smaller business. So the purpose of the page is to clearly showcase the message in a web 3.0 fashion, good design looks but function should always be the main focus.Further more we are looking for a long term relationship with a good designer / design company that can help us design the future web sites for our customers as well.

We need you to understand web, not just design. You need to be up to date with how web looks and works, and how to make it as simple and easy to use as possible for the customer and at the same time good looking.

Colors and layout are free to choose, but we really like the kind of layout that forkcomet.com has so feel free to be inspired by them.

We want all of the pages design, but the main/landing page will be the big part, the rest are small pages that will use the same design frame as the main page.

PS. We just want the design in photoshop or illustrator format, the website will then be built in word press by word press experts (let us know if you/company also possess this knowledge)

Target Market(s)

Small to medium sized business, mostly owner/entrepreneur driven companies.

Industry/Entity Type

Business

Font styles to use
Other font styles liked:
• Helvetica for the win

Requirements
Must have
• Great and simple design, a child should be able to understand the message and also enjoy reading it. Should be a funny website while still being professional, i.e. see postbadger.com for example.

```html
<!DOCTYPE html>
<html lang="en">
<head>
<meta charset="utf-8">
<title>Sitelaunch – Most convenient web ever</title>
<link href="https://fonts.googleapis.com/css2?family=Archivo+Narrow:wght@700&family=Open+Sans:wght@300;400&family=Arimo:wght@400;700&display=swap" rel="stylesheet">
<style>
:root{
  --brand:#2f6894;
  --band:#336d97;
  --hero-top:#3a6b95;
  --hero-mid:#6f94b7;
  --cloud:#e9eef5;
  --ink:#2b2b2b;
  --muted:#666;
  --rule:#dcdcdc;
  --footer:#3b3b3b;
  --footer-text:#d5d5d5;
  --chat:#5b636d;
  --white:#fff;
}
*{box-sizing:border-box;margin:0;padding:0}
html,body{width:887px;height:1200px;overflow:hidden;background:var(--white)}
body{position:relative;font-family:"Arimo",Helvetica,Arial,sans-serif;color:var(--ink)}
.abs{position:absolute}
.site-header{position:absolute;left:0;top:0;width:887px;height:57px;background:var(--white)}
.logo{left:128px;top:12px;font-weight:700;font-size:21px;color:var(--brand);letter-spacing:-.3px;line-height:1}
.logo-tag{left:129px;top:36px;font-size:8.5px;color:#777;letter-spacing:.6px}
.main-nav a{position:absolute;top:26px;font-size:8.5px;color:#333;text-decoration:none}
.lang-select{left:681px;top:20px;width:80px;height:19px;border:1px solid #aaa;font-size:7.5px;color:#444;padding:4px 8px}
.lang-select::after{content:"";position:absolute;right:8px;top:8px;border:3px solid transparent;border-top-color:#555}
.hero{left:0;top:57px;width:887px;height:349px;
  background:linear-gradient(180deg,var(--hero-top) 0%,var(--hero-mid) 55%,#c9d7e6 78%,var(--cloud) 100%)}
.hero-person{left:158px;top:62px;width:172px;height:236px;border-radius:80px 80px 10px 10px;
  background:linear-gradient(180deg,#b8a494 0%,#e6e6ea 45%,#f1f1f3 100%);opacity:.9}
.hero-title{left:335px;top:140px;font-family:"Archivo Narrow","Arial Narrow",sans-serif;font-weight:700;font-size:38px;color:var(--white);line-height:1}
.hero-sub{left:335px;top:183px;font-weight:700;font-size:25px;color:var(--white);line-height:1}
.hero-text{left:335px;top:219px;width:380px;font-size:10px;line-height:16.5px;color:#eef3f8}
.who-title{left:0;width:887px;top:438px;text-align:center;font-family:"Archivo Narrow","Arial Narrow",sans-serif;font-weight:700;font-size:24px;color:var(--brand)}
.who-text{left:150px;width:587px;top:479px;text-align:center;font-size:8.3px;line-height:16.5px;color:#333}
.rule{left:127px;top:534px;width:634px;height:1px;background:var(--rule)}
.chat-tab{left:787px;top:421px;width:100px;height:47px;background:var(--chat);color:var(--white)}
.chat-tab b{position:absolute;left:46px;top:15px;font-weight:400;font-size:8.5px}
.chat-tab small{position:absolute;left:46px;top:29px;font-size:6.5px;font-weight:700}
.feature{position:absolute;top:562px;width:195px;text-align:center}
.feature .media{width:195px;height:101px}
.feature h3{margin-top:20px;font-family:"Open Sans",sans-serif;font-weight:400;font-size:12.5px;color:#222}
.feature p{margin:10px auto 0;width:170px;font-size:7.6px;line-height:15.3px;color:#333}
.calc-band{left:0;top:805px;width:887px;height:263px;background:var(--band);color:var(--white)}
.calc-title{left:0;width:887px;top:27px;text-align:center;font-family:"Archivo Narrow","Arial Narrow",sans-serif;font-weight:700;font-size:21px}
.calc-sub{left:0;width:887px;top:55px;text-align:center;font-family:"Open Sans",sans-serif;font-weight:300;font-size:18px}
.field label{position:absolute;top:103px;font-size:7.5px;white-space:nowrap}
.field .box{position:absolute;top:120px;width:151px;height:20px;border:1px solid #e8eef4}
.select-box{font-size:7.5px;padding:5px 8px;background:var(--band)}
.select-box::after{content:"";position:absolute;right:7px;top:8px;border:3px solid transparent;border-top-color:#fff}
.btn{position:absolute;left:610px;width:151px;height:24px;background:linear-gradient(#f4f4f4,#d9dde1);color:#444;font-size:8px;text-align:center;line-height:24px;letter-spacing:.2px}
.calc-result{left:129px;top:185px;width:470px;font-size:7.6px;line-height:15.3px}
.clients{left:0;top:1068px;width:887px;height:61px;background:var(--white)}
.client{position:absolute;top:23px;font-weight:700;font-size:14px;color:#8a8a8a;white-space:nowrap}
.client i{display:inline-block;width:10px;height:10px;border-radius:50%;background:#8a8a8a;margin-right:4px;vertical-align:-1px}
.site-footer{left:0;top:1129px;width:887px;height:71px;background:var(--footer);color:var(--footer-text)}
.footer-nav a{position:absolute;top:22px;font-size:7.8px;color:var(--footer-text);text-decoration:none}
.copyright{left:128px;top:43px;font-size:7.5px}
.follow{left:617px;top:32px;font-size:7.5px}
.social{position:absolute;top:26px;width:20px;height:20px;border-radius:50%;background:#6b6b6b}
</style>
</head>
<body>

<header class="site-header">
  <div class="abs logo">Sitelaunch</div>
  <div class="abs logo-tag">Most convenient web ever</div>
  <nav class="main-nav">
    <a style="left:325px">How it works</a>
    <a style="left:414px">FAQ</a>
    <a style="left:457px">What people think?</a>
    <a style="left:562px">Order</a>
    <a style="left:618px">Contact us</a>
  </nav>
  <div class="abs lang-select">English</div>
</header>

<section class="abs hero" role="img" aria-label="Blue sky illustration with paper planes, dotted flight paths and white clouds along the bottom">
</section>
<div class="abs hero-person" role="img" aria-label="Photo of a woman holding a sign with a question mark"></div>
<svg class="abs" style="left:48px;top:165px" width="16" height="36" viewBox="0 0 16 36"><polyline points="13,2 3,18 13,34" fill="none" stroke="#cfdbe7" stroke-width="1.5"/></svg>
<svg class="abs" style="left:822px;top:165px" width="16" height="36" viewBox="0 0 16 36"><polyline points="3,2 13,18 3,34" fill="none" stroke="#cfdbe7" stroke-width="1.5"/></svg>
<h1 class="abs hero-title">Site Launch</h1>
<h2 class="abs hero-sub">Most convenient web ever</h2>
<p class="abs hero-text">Lorem Ipsum as their default model text, and a search for 'lorem ipsum' will uncover many web sites still in their infancy. Various versions have evolved over the years...</p>

<h2 class="abs who-title">Who we are ?</h2>
<p class="abs who-text">Lorem Ipsum as their default model text, and a search for 'lorem ipsum' will uncover many web sites still in their infancy. Various versions have evolved over the years Lorem Ipsum as their default model text, and a search for 'lorem ipsum' will uncover many web sites still in their infancy.</p>
<div class="abs rule"></div>

<aside class="abs chat-tab">
  <svg class="abs" style="left:17px;top:15px" width="24" height="18" viewBox="0 0 24 18"><ellipse cx="10" cy="8" rx="9" ry="6" fill="#c9cdd2"/><path d="M5 12 L3 17 L10 13 Z" fill="#c9cdd2"/><ellipse cx="16" cy="10" rx="7" ry="5" fill="#e3e6e9"/></svg>
  <b>Chat Online</b><small>Click here</small>
</aside>

<article class="feature" style="left:127px">
  <div class="media" role="img" aria-label="Photo of a woman looking up at a sketched rocket" style="background:linear-gradient(180deg,#4f78a8,#6d92bd)"></div>
  <h3>What is sitelaunch?</h3>
  <p>Lorem Ipsum as their default model text, and a search for 'lorem ipsum' will uncover many web sites still in their infancy. Various versions have evolved over the years...</p>
</article>
<article class="feature" style="left:346px">
  <div class="media" role="img" aria-label="Photo of banknotes flying out of a bright blue burst" style="background:radial-gradient(circle at 50% 55%,#e9f3fb,#4a8fc4 60%,#1f5c8e)"></div>
  <h3>What does it cost?</h3>
  <p>Lorem Ipsum as their default model text, and a search for 'lorem ipsum' will uncover many web sites still in their infancy. Various versions have evolved over the years...</p>
</article>
<article class="feature" style="left:566px">
  <div class="media" role="img" aria-label="Photo of a worried businessman at his desk" style="background:linear-gradient(90deg,#e6edf2,#b9cde0 60%,#7fa3c6)"></div>
  <h3>If you are unhappy?</h3>
  <p>Lorem Ipsum as their default model text, and a search for 'lorem ipsum' will uncover many web sites still in their infancy. Various versions have evolved over the years...</p>
</article>

<section class="abs calc-band">
  <h2 class="abs calc-title">Test your website now!</h2>
  <p class="abs calc-sub">How many more customers could you get every month?</p>
  <div class="field"><label style="left:128px">Visitors per month</label><div class="box" style="left:127px"></div></div>
  <div class="field"><label style="left:289px">Current conversion rate in %</label><div class="box" style="left:288px"></div></div>
  <div class="field"><label style="left:450px">Improve conversion rate, 13%</label><div class="box" style="left:449px"></div></div>
  <div class="field"><label style="left:611px">Average purchase in SEK</label><div class="box select-box" style="left:610px">Sek</div></div>
  <div class="btn" style="top:147px">CALCULATE</div>
  <div class="btn" style="top:183px">MOST CONVENIENT WEB EVER</div>
  <p class="abs calc-result">&lt;spit out, numberofvisitors x goalofconversionrateincrease&gt; of extra customers or potential customers every month with an increase of &lt;goalofconversion&gt; on your website. This would also mean &lt;numberofvisitors x goalofconversionrateincrease x Average purchase in SEK&gt; in extra revenue every month!</p>
</section>

<section class="abs clients">
  <span class="client" style="left:147px">Nordvale</span>
  <span class="client" style="left:250px"><i></i>Kestrin</span>
  <span class="client" style="left:355px"><i></i>Ulvo</span>
  <span class="client" style="left:453px">Brightform</span>
  <span class="client" style="left:565px"><i></i>Havgas</span>
  <span class="client" style="left:652px"><i></i>Openfield</span>
</section>

<footer class="abs site-footer">
  <nav class="footer-nav">
    <a style="left:128px">Home</a>
    <a style="left:169px">How it works</a>
    <a style="left:233px">FAQ</a>
    <a style="left:269px">Privacy Policy</a>
    <a style="left:337px">What people think?</a>
    <a style="left:423px">Order</a>
    <a style="left:463px">Contact us</a>
  </nav>
  <p class="abs copyright">© 2014. Site Launch. All Rights Reserved</p>
  <span class="abs follow">Follow us :</span>
  <span class="social" style="left:658px"></span>
  <span class="social" style="left:685px"></span>
  <span class="social" style="left:712px"></span>
  <span class="social" style="left:739px"></span>
</footer>

</body>
</html>
```